Thornvale Group needs a business card design

We need a new business card design using the logo recently selected in a logo competition on Pixel Bazaar. Our business is a consultancy specializing in aviation and energy and the winning business card design will promote an image of precision and professionalism with creativity.

Please use the logo with the name on the front of the card and use a complementary font. Make the back white with either the light grey or dark grey logo.

Target Market(s)

Senior finance and legal leaders at aviation and energy companies

Industry/Entity Type

Management Consulting

Contact Information for Business Card

Peter Castrell
President
Thornvale Group

www.thornvalegroup.example

(555) 204-6391
pc@thornvalegroup.example

Requirements
Must have
• Professional font that goes well with the logo font

```html
<!DOCTYPE html>
<html lang="en">
<head>
<meta charset="utf-8">
<title>Thornvale Group – Business Card</title>
<link rel="stylesheet" href="https://fonts.googleapis.com/css2?family=Open+Sans:ital,wght@0,400;0,600;0,700;1,700&display=swap">
<style>
  :root {
    --navy: #123f6e;
    --ink: #1d1d1f;
    --paper: #ffffff;
    --paper-shade: #f1f2f3;
    --backdrop: #e4e5e7;
    --band-text: #ffffff;
  }
  * { box-sizing: border-box; margin: 0; padding: 0; }
  html, body {
    width: 1200px; height: 864px; overflow: hidden;
    background: var(--backdrop);
    font-family: "Open Sans", Arial, sans-serif;
  }
  .canvas {
    position: relative; width: 1200px; height: 864px;
  }
  .card {
    position: absolute; left: 320px; width: 560px; height: 320px;
    background: var(--paper);
    box-shadow: 0 2px 6px rgba(0,0,0,0.12);
    overflow: hidden;
  }
  .card--front { top: 82px; }
  .card--back {
    top: 462px;
    background: linear-gradient(180deg, var(--paper-shade) 0%, var(--paper) 55%);
  }

  /* Front */
  .wordmark {
    position: absolute; left: 0; right: 0; top: 118px;
    display: flex; align-items: center; justify-content: center; gap: 16px;
  }
  .wordmark__square {
    width: 30px; height: 30px; background: var(--navy);
  }
  .wordmark__name {
    color: var(--navy); font-weight: 400; font-size: 34px;
    letter-spacing: 5px; text-transform: uppercase; line-height: 1;
  }

  /* Back */
  .back-mark {
    position: absolute; left: 0; right: 0; top: 52px;
    display: flex; align-items: center; justify-content: center; gap: 12px;
  }
  .back-mark__square { width: 22px; height: 22px; background: var(--navy); }
  .back-mark__name {
    color: var(--navy); font-weight: 400; font-size: 24px;
    letter-spacing: 4px; text-transform: uppercase; line-height: 1;
  }
  .person {
    position: absolute; left: 44px; top: 150px; text-align: right; width: 180px;
  }
  .person__name { color: var(--navy); font-weight: 700; font-size: 19px; line-height: 1.2; }
  .person__title { color: var(--ink); font-size: 13px; margin-top: 4px; }
  .contact {
    position: absolute; left: 300px; top: 158px; list-style: none;
    color: var(--ink); font-size: 14px;
  }
  .contact li { display: flex; align-items: center; gap: 10px; margin-bottom: 6px; }
  .contact svg { width: 12px; height: 12px; fill: var(--navy); flex: none; }
  .band {
    position: absolute; left: 0; right: 0; bottom: 0; height: 108px;
    background: var(--navy); color: var(--band-text);
    padding: 14px 0 0 36px;
  }
  .band__tagline { font-weight: 700; font-style: italic; font-size: 18px; }
  .band__sectors { font-weight: 600; font-size: 14px; margin-top: 8px; }
  .band__sep { margin: 0 6px; }
</style>
</head>
<body>
<main class="canvas">
  <section class="card card--front" aria-label="Card front">
    <div class="wordmark">
      <span class="wordmark__square"></span>
      <span class="wordmark__name">Thornvale Group</span>
    </div>
  </section>

  <section class="card card--back" aria-label="Card back">
    <div class="back-mark">
      <span class="back-mark__square"></span>
      <span class="back-mark__name">Thornvale Group</span>
    </div>

    <div class="person">
      <p class="person__name">Peter Castrell</p>
      <p class="person__title">President</p>
    </div>

    <ul class="contact">
      <li>
        <svg viewBox="0 0 24 24" aria-hidden="true"><path d="M6.6 10.8a15.1 15.1 0 0 0 6.6 6.6l2.2-2.2a1 1 0 0 1 1-.25 11.4 11.4 0 0 0 3.6.57 1 1 0 0 1 1 1V20a1 1 0 0 1-1 1A17 17 0 0 1 3 4a1 1 0 0 1 1-1h3.5a1 1 0 0 1 1 1c0 1.25.2 2.45.57 3.57a1 1 0 0 1-.25 1z"/></svg>
        <span>(555) 204-6391</span>
      </li>
      <li>
        <svg viewBox="0 0 24 24" aria-hidden="true"><path d="M2 5h20v14H2z M2 5l10 8 10-8" fill="var(--navy)"/><path d="M3 6l9 7 9-7" fill="none" stroke="#fff" stroke-width="1.6"/></svg>
        <span>pc@thornvalegroup.example</span>
      </li>
    </ul>

    <div class="band">
      <p class="band__tagline">Finance and Strategy Consulting</p>
      <p class="band__sectors">Aviation<span class="band__sep">&lt;</span>Manufacturing<span class="band__sep">&lt;</span>Energy</p>
    </div>
  </section>
</main>
</body>
</html>
```